Fitness Nutrition Book to be designed

My business is an Online Fitness Training Business.
I have created a nutritional booklet that each online client will receive.
The booklet in total is 17 pages, which includes front and back cover.
Text has all been completed.
The booklet should be easy to read and using colors that convey energy, such as blues, blacks, greys, yellows, reds, etc.
I do not have photos of clients working out, but I would like to use photos that represent fitness.
Appropriate items would be Kettle Bells, Dumbbells, Battle Ropes and Slam balls
I would like the interior pages to have motivational quotes, creatively and eye catching, placed on the pages.
Quotes such as:
"If it doesn't challenge you, It wont change you!"
"Train insane or remain the same"
"Sweat is Fat Crying"
"Sore Today Strong Tomorrow"
"Motivation is what gets you started, Habit is what keeps you going"
"3 Months from now you will thank yourself"
These are all quotes that I found from googling "Motivational Fitness Quote Images."
The cover should contain our            VelroDyn logo.
with                                 "You are a part of the fitness revolution!"
Meal Plan
The only interior page that will change is the meal plan portion.
There are 5 different meal plans, 1200, 1500, 1750, 2000 & 2200 calories
I would also like the correct caloric number of the interior meal plan to be placed somewhere on the cover page as well, so that by looking at the cover page, the 1200 calorie meal plan book would be easily found and distinguishable from the 1500 calorie meal plan book.
Thank you!

Target Market(s)
Target market:
25-45 year old
60% female / 40% male
has at least one child
middle income
Gets coffee at brewlocke
States that they, "want to tone up"
Currently goes to the gym maybe 1-3 x per week
Industry/Entity Type
Business
Requirements
Must have
- Clear, easy to read and follow
- I have included a file labeled "Competitors Example" This is one of my old packets that I had made years ago. I do not like this style of cover with tons of pictures
- And the new packet I am wanting to have created should look much better.

Should not have
- This packet should not be plain and boring. There should not be any page that is simply white with small black text.

```html
<!DOCTYPE html>
<html lang="en">
<head>
<meta charset="utf-8">
<title>VelroDyn Nutrition Booklet – Pages 12–15</title>
<link href="https://fonts.googleapis.com/css2?family=Fira+Sans:wght@500;600&family=Roboto+Condensed:wght@300;400;700&family=Open+Sans:wght@400;600;700&family=Oswald:wght@600;700&display=swap" rel="stylesheet">
<style>
:root{
  --stage:#3d3d3d;
  --blue:#1f75c4;
  --blue-dark:#185fa3;
  --paper:#ffffff;
  --cat:#a8aaad;
  --shade:#e4e5e7;
  --ink:#3a3a3a;
  --lime:#c8d33a;
  --black:#111;
}
*{box-sizing:border-box;margin:0;padding:0}
html,body{width:910px;height:1200px;overflow:hidden;background:var(--stage)}
body{position:relative;font-family:"Open Sans",sans-serif;color:var(--ink)}
.spread{position:absolute;left:50px;width:800px;height:517px;display:flex;box-shadow:0 4px 14px rgba(0,0,0,.45)}
.spread.top{top:81px}
.spread.bottom{top:643px}
.page{position:relative;width:400px;height:517px;background:var(--paper);overflow:hidden}
.page.left{background:linear-gradient(to right,#fff 80%,#ececec 97%,#dcdcdc)}
.page.right{background:linear-gradient(to left,#fff 80%,#ececec 97%,#dcdcdc)}
.masthead{height:58px;background:var(--blue);display:flex;align-items:flex-end;justify-content:center;padding-bottom:8px}
.masthead h2{font-family:"Fira Sans",sans-serif;font-weight:600;color:#fff;font-size:17px;letter-spacing:.2px}
.folio{position:absolute;bottom:0;width:10px;height:22px;background:var(--blue);color:#fff;font-size:5px;text-align:center;padding-top:3px}
.left .folio{left:24px}
.right .folio{right:23px}
.group{position:absolute;left:23px;width:354px}
.tab{display:inline-block;background:var(--blue);color:#fff;font-family:"Roboto Condensed",sans-serif;font-weight:700;font-size:12.5px;padding:4px 8px 3px;border-radius:6px 6px 0 0}
.tbl{border-top:2px solid var(--blue)}
.cat{background:var(--cat);color:#fff;font-weight:600;font-size:8.5px;height:19px;line-height:19px;padding-left:8px}
.row{display:grid;grid-template-columns:66px 146px 1fr;height:18.8px;align-items:center;font-size:6.2px;padding-left:8px}
.row.s{background:var(--shade)}
.note{background:var(--shade);font-size:6px;padding:5px 8px 5px;line-height:1.6}
.note em{font-weight:700}
.photo{position:absolute;left:23px;top:259px;width:354px;height:216px;background:linear-gradient(160deg,#9a5a45 0%,#7d4536 45%,#3a2a26 78%,#151515 100%)}
.photo-quote{position:absolute;left:100px;top:286px;width:150px;font-family:"Oswald",sans-serif;font-weight:700;font-size:35px;line-height:.98;color:#111;text-align:center;text-transform:uppercase}
.faq-icon{position:absolute;left:162px;top:30px}
.faq-title{position:absolute;top:99px;width:100%;text-align:center;font-family:"Roboto Condensed",sans-serif;font-weight:700;color:var(--blue);font-size:14px}
.qa{position:absolute;width:172px;font-size:7px;line-height:1.42}
.qa h4{font-family:"Roboto Condensed",sans-serif;font-weight:300;color:var(--blue);font-size:11.5px;line-height:1.2;margin-bottom:9px}
.qa .label{color:var(--blue);font-weight:700}
.qa p+p{margin-top:8px}
.divider{position:absolute;border-top:1px dashed #9a9a9a}
.badge{position:absolute;left:24px;top:355px;width:142px;height:142px;border-radius:50%;background:var(--lime);display:flex;align-items:center;justify-content:center;text-align:center;font-family:"Oswald",sans-serif;font-weight:700;font-style:italic;font-size:22px;line-height:1.05;color:var(--black);text-transform:uppercase}
</style>
</head>
<body>

<!-- Spread: pages 12–13 -->
<div class="spread top">
  <article class="page left">
    <header class="masthead"><h2>VelroDyn Food Database</h2></header>
    <section class="group" style="top:74px">
      <h3 class="tab">PROTEINS</h3>
      <div class="tbl">
        <div class="cat">Beef</div>
        <div class="row s"><span>1 oz</span><span>Ground Beef (95% Lean)</span><span>6 grams protein</span></div>
        <div class="row"><span>1 oz</span><span>Beef Tenderloin</span><span>5 grams protein</span></div>
        <div class="row s"><span>1 oz</span><span>Filet Mignon</span><span>5 grams protein</span></div>
        <div class="cat">Eggs</div>
        <div class="row s"><span>1</span><span>Large Whole Egg</span><span>6 grams protein</span></div>
        <div class="row"><span>1</span><span>Extra-large Whole Egg</span><span>7 grams protein</span></div>
        <div class="row s"><span>1</span><span>Jumbo Whole Egg</span><span>8 grams protein</span></div>
        <div class="row"><span>1</span><span>Large Egg White</span><span>4 grams protein</span></div>
        <div class="row s"><span>½ Cup</span><span>Liquid Egg Whites</span><span>13 grams protein</span></div>
        <div class="cat">Dairy</div>
        <div class="row s"><span>1 oz</span><span>Fat Free (0%) Alpenmoor Greek Yogurt</span><span>3 grams protein</span></div>
        <div class="row"><span>1 oz</span><span>Non-fat Cottage Cheese</span><span>3 grams protein</span></div>
        <div class="row s"><span>1 oz</span><span>Low Fat Cottage Cheese (1%)</span><span>3 grams protein</span></div>
      </div>
    </section>
    <section class="group" style="top:378px">
      <h3 class="tab">STARCHY CARBOHYDRATES</h3>
      <div class="tbl">
        <div class="cat">Beans</div>
        <div class="row s"><span>¼ cup</span><span>Black Beans (cooked)</span><span>10 grams of carbohydrates</span></div>
        <div class="row"><span>¼ cup</span><span>Kidney Beans (cooked)</span><span>10 grams of carbohydrates</span></div>
      </div>
    </section>
    <span class="folio">12</span>
  </article>

  <article class="page right">
    <header class="masthead"><h2>VelroDyn Food Database</h2></header>
    <section class="group" style="top:74px">
      <h3 class="tab">STARCHY CARBOHYDRATES</h3>
      <div class="tbl">
        <div class="cat">Beans</div>
        <div class="row s"><span>¼ cup</span><span>Lima Beans (cooked)</span><span>10 grams of carbohydrates</span></div>
        <div class="row"><span>¼ cup</span><span>Pinto Beans (cooked)</span><span>11 grams of carbohydrates</span></div>
        <div class="row s"><span>¼ cup</span><span>Lentils (cooked)</span><span>10 grams of carbohydrates</span></div>
        <div class="row"><span>¼ cup</span><span>Refried Beans (vegetarian)</span><span>10 grams of carbohydrates</span></div>
        <div class="cat">Rice</div>
        <div class="row s"><span>¼ cup</span><span>Quinoa</span><span>10 grams of carbohydrates</span></div>
        <div class="row"><span>¼ cup</span><span>Brown Rice (cooked)</span><span>12 grams of carbohydrates</span></div>
        <div class="row s"><span>1</span><span>Rice Cake</span><span>7 grams of carbohydrates</span></div>
        <div class="cat">Bread</div>
        <div class="row s"><span>1 slice</span><span>Harvestine 4:9 Bread</span><span>15 grams of carbohydrates</span></div>
        <div class="row"><span>1</span><span>Harvestine English Muffin</span><span>30 grams of carbohydrates</span></div>
        <div class="row s"><span>1</span><span>Brown Rice Tortilla</span><span>24 grams of carbohydrates</span></div>
        <div class="cat">Starchy Vegetables</div>
        <div class="row s"><span>1 oz</span><span>Yams</span><span>6 grams of carbohydrates</span></div>
        <div class="cat">Fibrous Carbohydrates</div>
        <div class="note">Eat as many vegetables as you would like such as green leafy veggies, peppers, broccoli, cucumbers, etc.<br><em>*Do not eat carrots, peas, corn, russet potatoes, Yukon potatoes</em></div>
      </div>
    </section>
    <span class="folio">13</span>
  </article>
</div>

<!-- Spread: pages 14–15 -->
<div class="spread bottom">
  <article class="page left">
    <header class="masthead"><h2>VelroDyn Food Database</h2></header>
    <section class="group" style="top:75px">
      <h3 class="tab">FATS</h3>
      <div class="tbl">
        <div class="cat">Nuts and Seeds</div>
        <div class="row s"><span>1 oz</span><span>Mixed Nuts</span><span>15 grams of fat</span></div>
        <div class="row"><span>1 oz</span><span>(22 Almonds)</span><span>15 grams of fat</span></div>
        <div class="row s"><span>12</span><span>Almonds</span><span>7.5 grams of fat</span></div>
        <div class="row"><span>1 TBS</span><span>Almond Butter</span><span>9 grams of fat</span></div>
        <div class="row s"><span>1/3</span><span>Avocado</span><span>8 grams of fat</span></div>
        <div class="row"><span>1 TBS</span><span>Chia Seeds</span><span>4 grams of fat</span></div>
      </div>
    </section>
    <div class="photo" role="img" aria-label="Photo of a red brick wall with a kettlebell and dumbbells on a dark gym floor"></div>
    <p class="photo-quote">Get Fit Don't Quit</p>
    <span class="folio">14</span>
  </article>

  <article class="page right">
    <svg class="faq-icon" width="76" height="64" viewBox="0 0 76 64" aria-hidden="true">
      <circle cx="28" cy="26" r="25" fill="var(--blue)"/>
      <path d="M14 44 L10 58 L26 48 Z" fill="var(--blue)"/>
      <path d="M17 27 l7 7 l14 -15" stroke="#fff" stroke-width="5" fill="none" stroke-linecap="round" stroke-linejoin="round"/>
      <circle cx="56" cy="40" r="17" fill="#fff" stroke="var(--blue)" stroke-width="3"/>
      <path d="M62 55 L68 63 L54 57" fill="#fff" stroke="var(--blue)" stroke-width="3" stroke-linejoin="round"/>
      <text x="56" y="47" text-anchor="middle" font-family="Open Sans,sans-serif" font-weight="700" font-size="18" fill="var(--blue)">?</text>
    </svg>
    <h3 class="faq-title">Frequently Asked Questions</h3>

    <div class="qa" style="left:23px;top:141px">
      <h4>Question: Can I have coffee?</h4>
      <p><span class="label">Answer:</span><br>Yes! It's not the coffee that causes issues. It's all of the "stuff" that we put into the coffee. Stay away from natural and artificial sweeteners and instead of creamer, use almond milk or coconut milk</p>
    </div>
    <div class="divider" style="left:23px;top:225px;width:172px"></div>
    <div class="qa" style="left:23px;top:237px">
      <h4>Question: What about seasonings?</h4>
      <p><span class="label">Answer:</span><br>Season your food up!! You just want to refrain from salts and sugars, but feel free to get creative. I will often use fresh cut salsas and pico de gallo for my meats. Some other seasonings that you can use are Mrs. Zestle found at local grocery stores and you can also order Savor Kin seasonings online.</p>
    </div>

    <div class="qa" style="left:205px;top:141px">
      <h4>Question: Why is there no fruit on the meal plan other than an apple?</h4>
      <p><span class="label">Answer:</span><br>Most fruit is full of sugar. We call fruit, "Natures Candy Bar" and we want to eliminate sugars as much as possible. If you are going to have fruit, you should only have a small amount of berries within the first few meals of the day.</p>
    </div>
    <div class="divider" style="left:205px;top:247px;width:172px"></div>
    <div class="qa" style="left:205px;top:259px">
      <h4>Question: What kind of protein powder should I use?</h4>
      <p><span class="label">Answer:</span><br>There are a ton of options out there, but unfortunately very few great options. Whey protein isolate or concentrate powder can be utilized by the body very efficiently and is a great option. Personally I have been using Corevia Prime Standard, which can be found at Bulkmart, Vitalo Shop, NTR Stores etc.</p>
      <p>My rule of thumb for protein powders is to look at the ingredients. You want something with approximately 8 or less ingredients. You will find some of the options have an entire laundry list of ingredients and that's a pretty clear sign that it has a lot of fillers, chemicals and is a lower quality of protein.</p>
    </div>

    <div class="badge">Sweat is<br>Fat Crying</div>
    <span class="folio">15</span>
  </article>
</div>

</body>
</html>
```